Redesign of business card for Cedar Ridge Mechanical

We are looking for a new design for our business cards for Cedar Ridge Mechanical. We are a plumbing & HVAC construction company, operating on the West Coast of Canada and USA. Logo attached.
Industry/Entity Type
Construction - Plumbing & HVAC
Contact Information for Business Card
Name, address, phone numbers, email, website address
Look and feel
Each slider illustrates characteristics of the customer's brand and the style your logo design should communicate.

```html
<!DOCTYPE html>
<html lang="en">
<head>
<meta charset="utf-8">
<title>Cedar Ridge Mechanical – Business Card</title>
<link rel="stylesheet" href="https://fonts.googleapis.com/css2?family=Open+Sans:wght@400;600;700&display=swap">
<style>
  :root {
    --page-bg: #e9e6e1;
    --card-frost: #dcdad6;
    --card-black: #0b0b0b;
    --accent-taupe: #8c826f;
    --name-gold: #d9c7a4;
    --text-light: #e4dccd;
    --brand-dark: #222222;
  }
  html, body {
    margin: 0;
    width: 1200px;
    height: 1047px;
    overflow: hidden;
    background: var(--page-bg);
    font-family: "Open Sans", Arial, sans-serif;
  }
  .business-card {
    position: absolute;
    left: 100px;
    top: 251px;
    width: 1000px;
    height: 545px;
    border-radius: 26px;
    overflow: hidden;
    box-shadow: 0 10px 30px rgba(0,0,0,0.18);
  }
  .card-shapes {
    position: absolute;
    inset: 0;
  }
  .brand-block {
    position: absolute;
    left: 60px;
    top: 225px;
    display: flex;
    align-items: center;
    gap: 16px;
  }
  .brand-mark {
    width: 40px;
    height: 40px;
    background: var(--brand-dark);
  }
  .brand-name {
    font-weight: 600;
    font-size: 34px;
    color: var(--brand-dark);
    letter-spacing: 0.5px;
    white-space: nowrap;
  }
  .contact-panel {
    position: absolute;
    left: 622px;
    top: 88px;
    color: var(--text-light);
  }
  .person-name {
    margin: 0;
    font-weight: 700;
    font-size: 32px;
    line-height: 38px;
    color: var(--name-gold);
    letter-spacing: 0.5px;
  }
  .person-title {
    margin: 0 0 0 3px;
    font-size: 24px;
    line-height: 30px;
    color: var(--name-gold);
  }
  .address {
    margin: 58px 0 0 -8px;
    font-size: 25px;
    line-height: 34px;
  }
  .contact-list {
    list-style: none;
    margin: 36px 0 0 -8px;
    padding: 0;
    font-size: 25px;
    line-height: 34px;
  }
  .contact-list li {
    display: flex;
    align-items: center;
    gap: 10px;
  }
  .contact-icon {
    width: 20px;
    height: 20px;
    fill: var(--text-light);
  }
</style>
</head>
<body>
  <div class="business-card">
    <svg class="card-shapes" width="1000" height="545" viewBox="0 0 1000 545">
      <rect width="1000" height="545" fill="var(--card-frost)"/>
      <path d="M458 0 C560 110 600 300 420 545 L470 545 C620 330 600 120 524 0 Z" fill="var(--accent-taupe)"/>
      <path d="M510 0 C610 130 640 330 462 545 L1000 545 L1000 0 Z" fill="var(--card-black)"/>
    </svg>

    <div class="brand-block">
      <span class="brand-mark"></span>
      <span class="brand-name">Cedar Ridge Mechanical</span>
    </div>

    <div class="contact-panel">
      <h1 class="person-name">DANIEL HARPER</h1>
      <p class="person-title">Managing Director</p>
      <p class="address">Your address, City<br>State, Zip 1234</p>
      <ul class="contact-list">
        <li>
          <svg class="contact-icon" viewBox="0 0 24 24"><path d="M6.6 10.8a15 15 0 0 0 6.6 6.6l2.2-2.2c.3-.3.7-.4 1-.2 1.1.4 2.3.6 3.6.6.6 0 1 .4 1 1V20c0 .6-.4 1-1 1A17 17 0 0 1 3 4c0-.6.4-1 1-1h3.5c.6 0 1 .4 1 1 0 1.3.2 2.5.6 3.6.1.3 0 .7-.2 1z"/></svg>
          <span>123 456 789</span>
        </li>
        <li>
          <svg class="contact-icon" viewBox="0 0 24 24"><path d="M2 6h20v13H2z M3.5 7.5 12 13l8.5-5.5" stroke="var(--card-black)" stroke-width="1.5"/></svg>
          <span>info@yourgmail.com</span>
        </li>
        <li>
          <svg class="contact-icon" viewBox="0 0 24 24"><circle cx="12" cy="12" r="10"/><path d="M2 12h20M12 2c3 3 3 17 0 20M12 2c-3 3-3 17 0 20" stroke="var(--card-black)" stroke-width="1.5" fill="none"/></svg>
          <span>www.yourwebsite.com</span>
        </li>
      </ul>
    </div>
  </div>
</body>
</html>
```